Need Business Card ASAP

We need a business card design for a meeting coming up in a few days. The company name is Harlow Ridge Building and Construction and the logo is attached. Something clean, cool, and contemporary that we can get to a printer right away. Attached is the business card for Volmar Energy, an affiliated company, which we like. Instead of the hawk on the back, you could use the attached "D". We'll also be needing matching letterhead in the near future, so ideas for that are welcome.

```html
<!DOCTYPE html>
<html lang="en">
<head>
<meta charset="utf-8">
<title>Harlow Ridge Building &amp; Construction – Business Card</title>
<link rel="stylesheet" href="https://fonts.googleapis.com/css2?family=Source+Sans+3:wght@400;600;700&display=swap">
<style>
  :root {
    --page: #efece4;
    --card-white: #ffffff;
    --ink: #3a3a3a;
    --ink-soft: #555555;
    --gold: #bfb58a;
    --gold-deep: #a99d6b;
    --band-black: #1e1e1e;
    --back-top: #c3bd98;
    --back-bottom: #e6e3d4;
  }
  * { box-sizing: border-box; margin: 0; padding: 0; }
  html, body { width: 1034px; height: 1200px; overflow: hidden; }
  body {
    background: var(--page);
    font-family: "Source Sans 3", "Helvetica Neue", Arial, sans-serif;
    color: var(--ink);
    position: relative;
  }
  .card {
    position: absolute;
    left: 73px;
    width: 889px;
    height: 507px;
    overflow: hidden;
    box-shadow: 0 2px 8px rgba(0,0,0,.18);
  }
  .card--front { top: 56px; background: var(--card-white); }
  .card--back {
    top: 597px;
    background: linear-gradient(180deg, var(--back-top) 0%, var(--back-bottom) 100%);
  }
  .front-wave { position: absolute; left: 0; top: 0; width: 889px; height: 200px; }
  .company-name {
    position: absolute; left: 50px; top: 58px;
    font-size: 28px; font-weight: 600; line-height: 1.3; color: var(--ink);
  }
  .address {
    position: absolute; right: 62px; top: 130px;
    text-align: right; font-size: 20px; line-height: 1.5; color: var(--ink);
  }
  .brand-tile {
    position: absolute; left: 49px; top: 203px; width: 172px; height: 218px;
    background: linear-gradient(160deg, #d6d0b2 0%, var(--gold-deep) 100%);
    display: flex; align-items: center; justify-content: center;
    text-align: center;
  }
  .brand-tile__name {
    font-size: 24px; font-weight: 600; line-height: 1.15; color: var(--band-black);
  }
  .contact {
    position: absolute; right: 62px; top: 250px; text-align: right;
  }
  .contact__name { font-size: 30px; font-weight: 700; color: var(--gold); line-height: 1.1; }
  .contact__title { font-size: 20px; font-weight: 600; color: var(--ink-soft); margin-bottom: 14px; }
  .contact__line {
    display: flex; justify-content: flex-end; align-items: center; gap: 8px;
    font-size: 22px; line-height: 38px; color: var(--ink);
  }
  .contact__line svg { width: 16px; height: 16px; fill: var(--ink); }
  .web-band {
    position: absolute; left: 0; bottom: 0; width: 100%; height: 51px;
    background: var(--band-black);
    display: flex; justify-content: flex-end; align-items: center; padding-right: 62px;
    color: #ffffff; font-size: 22px; letter-spacing: 1px;
  }
  .back-brand {
    position: absolute; left: 0; right: 0; top: 170px;
    display: flex; justify-content: center; align-items: center; gap: 22px;
  }
  .back-brand__mark { width: 70px; height: 70px; background: var(--card-white); }
  .back-brand__name {
    font-size: 46px; font-weight: 600; color: var(--band-black); line-height: 1.1;
  }
  .back-web {
    position: absolute; left: 0; right: 0; bottom: 22px;
    text-align: center; font-size: 24px; font-weight: 700; letter-spacing: 2px;
    color: var(--ink-soft);
  }
</style>
</head>
<body>

<section class="card card--front">
  <svg class="front-wave" viewBox="0 0 889 200" aria-hidden="true">
    <defs>
      <linearGradient id="silver" x1="0" x2="1" y1="0" y2="0">
        <stop offset="0" stop-color="#ffffff"/>
        <stop offset="0.45" stop-color="#f4f4f4"/>
        <stop offset="0.75" stop-color="#d4d4d4"/>
        <stop offset="1" stop-color="#e6e6e6"/>
      </linearGradient>
    </defs>
    <path d="M0,22 C260,8 420,50 889,42 L889,112 C560,108 420,118 300,150 C200,165 80,162 0,160 Z" fill="url(#silver)"/>
    <path d="M0,22 C260,8 420,50 889,42" fill="none" stroke="var(--gold)" stroke-width="3"/>
    <path d="M0,160 C80,162 200,165 300,150 C420,118 560,108 889,112" fill="none" stroke="var(--gold)" stroke-width="3"/>
  </svg>

  <h1 class="company-name">Harlow Ridge Building<br>&amp; Construction</h1>

  <p class="address">00, Complex Name<br>Street, City 00000</p>

  <div class="brand-tile">
    <span class="brand-tile__name">Harlow<br>Ridge</span>
  </div>

  <div class="contact">
    <p class="contact__name">Your Name</p>
    <p class="contact__title">Title</p>
    <p class="contact__line">
      <svg viewBox="0 0 16 16"><path d="M3 1h3l1.5 4-2 1.3a9 9 0 0 0 4.2 4.2L11 8.5l4 1.5v3a2 2 0 0 1-2 2A12 12 0 0 1 1 3a2 2 0 0 1 2-2z"/></svg>
      (123) 456-7890
    </p>
    <p class="contact__line">
      <svg viewBox="0 0 16 16"><path d="M5 0h6a1 1 0 0 1 1 1v14a1 1 0 0 1-1 1H5a1 1 0 0 1-1-1V1a1 1 0 0 1 1-1zm1 2v9h4V2z"/></svg>
      (123) 456-7890
    </p>
    <p class="contact__line">
      <svg viewBox="0 0 16 16"><path d="M1 4h14v9H1zm1 1.2V6l6 4 6-4v-.8L8 9z"/></svg>
      yourname@harlowridge.com
    </p>
  </div>

  <div class="web-band">www.harlowridge.com</div>
</section>

<section class="card card--back">
  <div class="back-brand">
    <span class="back-brand__mark"></span>
    <span class="back-brand__name">Harlow Ridge</span>
  </div>
  <p class="back-web">www.harlowridgebuilding.com</p>
</section>

</body>
</html>
```